Ad Banner for Lantern Post Hub

This banner is used in "Bright Lantern" web site. This web site provides a single place for all employees to ask questions related to work. There will be dedicated subject matter experts to respond to all questions. The web site also provides "Guild Map" where employee can see the list of all experts in the company.
1. Banner size: 940x380
2. Business background: Provides maintenance, design and engineering, construction, machinery operation, material procurement and production management services for petrochemical and refinery business
3. We would like to see designs that
- Promote the ask questions in "Bright Lantern" system
- Promote that company has experts in the areas of "Maintenance and Engineering" and can be found in "Guild Map"
- Encourage employees to advocate himself to be an expert by sending an email to a specific email address.
- Do not include picture of real people in the banner

```html
<!DOCTYPE html>
<html lang="en">
<head>
<meta charset="utf-8">
<title>Lantern Post Hub – Be an Expert</title>
<link href="https://fonts.googleapis.com/css2?family=Montserrat:wght@600;700;800;900&display=swap" rel="stylesheet">
<style>
  :root {
    --sky-light: #6fd6f7;
    --sky-mid: #1ea6df;
    --sky-deep: #0a86c6;
    --headline-yellow: #ffc40c;
    --headline-yellow-deep: #f6a800;
    --navy: #0b4a86;
    --silver-top: #ffffff;
    --silver-bottom: #c9d3da;
    --button-top: #ffb21a;
    --button-bottom: #f28a00;
    --helmet-yellow: #f7b500;
    --tower-grey: #8c8f93;
  }

  * { margin: 0; padding: 0; box-sizing: border-box; }

  html, body {
    width: 1200px;
    height: 485px;
    overflow: hidden;
  }

  body {
    font-family: "Montserrat", "Helvetica Neue", Arial, sans-serif;
  }

  .banner {
    position: relative;
    width: 1200px;
    height: 485px;
    overflow: hidden;
    background:
      radial-gradient(ellipse 520px 420px at 240px 220px, var(--sky-light) 0%, rgba(111,214,247,0) 75%),
      linear-gradient(90deg, var(--sky-mid) 0%, var(--sky-mid) 55%, var(--sky-deep) 100%);
  }

  .hero-art {
    position: absolute;
    left: 112px;
    top: 22px;
    width: 280px;
    height: 430px;
    border-radius: 40px 40px 140px 140px;
    background: linear-gradient(180deg, var(--tower-grey) 0%, #b9bcbf 42%, var(--helmet-yellow) 50%, #e89d00 100%);
    opacity: 0.95;
  }

  .message {
    position: absolute;
    left: 512px;
    top: 0;
    width: 600px;
    text-align: center;
  }

  .lead-in {
    margin-top: 64px;
    font-size: 60px;
    font-weight: 800;
    line-height: 1;
    letter-spacing: 0.5px;
    color: var(--silver-top);
    background: linear-gradient(180deg, var(--silver-top) 0%, var(--silver-bottom) 100%);
    -webkit-background-clip: text;
    background-clip: text;
    -webkit-text-fill-color: transparent;
  }

  .headline {
    margin-top: 6px;
    font-size: 124px;
    font-weight: 800;
    line-height: 1;
    letter-spacing: -2px;
    color: var(--headline-yellow);
    background: linear-gradient(180deg, var(--headline-yellow) 0%, var(--headline-yellow-deep) 100%);
    -webkit-background-clip: text;
    background-clip: text;
    -webkit-text-fill-color: transparent;
  }

  .field {
    margin-top: 10px;
    font-size: 37px;
    font-weight: 700;
    line-height: 1.15;
    color: var(--navy);
  }

  .cta {
    display: inline-block;
    margin-top: 28px;
    width: 246px;
    height: 50px;
    line-height: 50px;
    border-radius: 4px;
    background: linear-gradient(180deg, var(--button-top) 0%, var(--button-bottom) 100%);
    box-shadow: 0 2px 4px rgba(0, 40, 80, 0.3);
    color: #ffffff;
    font-size: 21px;
    font-weight: 700;
    text-decoration: none;
  }

  .contact {
    margin-top: 14px;
    font-size: 13px;
    font-weight: 700;
    line-height: 1.3;
    color: var(--navy);
  }
</style>
</head>
<body>
  <div class="banner">
    <div class="hero-art" role="img" aria-label="Illustration of city skyscrapers rising out of a yellow construction hard hat"></div>

    <div class="message">
      <p class="lead-in">BE AN</p>
      <h1 class="headline">EXPERT</h1>
      <p class="field">IN MAINTENANCE &amp;<br>ENGINEERING</p>
      <a class="cta" href="#">CLICK FOR MORE</a>
      <p class="contact">OR SEND AN EMAIL AT<br>INFO@BRIGHTLANTERN.COM</p>
    </div>
  </div>
</body>
</html>
```